holloway paving service

Needs to have phone number 0418259730 and email markholloway@brightmail.com.au.
ABN 62318470915
name mark holloway

For all your concreting solutions
Excavation
Exposed & colour concrete
House & shed slabs
Driveways
Landing & steps

Contact Information for Business Card

ph 0418259730
email markholloway@brightmail.com.au.
ABN 62318470915
name mark holloway

```html
<!DOCTYPE html>
<html lang="en">
<head>
<meta charset="UTF-8">
<title>Holloway Paving Service – Business Card</title>
<link rel="stylesheet" href="https://fonts.googleapis.com/css2?family=Montserrat:wght@700&family=Lato:wght@400&display=swap">
<style>
  :root {
    --backdrop: #2b2b2d;
    --card: #111112;
    --card-edge: #1b1b1d;
    --orange: #f26a1b;
    --grey: #8a8a8c;
    --light-grey: #b9b9bb;
    --rule: #4a4a4c;
  }
  * { margin: 0; padding: 0; box-sizing: border-box; }
  html, body {
    width: 1200px;
    height: 900px;
    overflow: hidden;
    background: var(--backdrop);
  }
  .canvas {
    width: 1200px;
    height: 900px;
    display: flex;
    flex-direction: column;
    align-items: center;
    justify-content: center;
    gap: 40px;
  }
  .card {
    position: relative;
    width: 560px;
    height: 320px;
    background: linear-gradient(160deg, var(--card-edge), var(--card) 60%);
    overflow: hidden;
  }
  .card__band {
    position: absolute;
    left: 0;
    right: 0;
    bottom: 0;
    height: 9px;
    background: var(--orange);
  }

  /* Front */
  .card--front {
    display: flex;
    align-items: center;
    justify-content: center;
    gap: 18px;
    padding-bottom: 9px;
  }
  .brand-mark {
    width: 56px;
    height: 56px;
    background: var(--orange);
  }
  .brand-divider {
    width: 2px;
    height: 86px;
    background: var(--orange);
  }
  .brand-text {
    display: flex;
    flex-direction: column;
    gap: 8px;
  }
  .brand-name {
    font-family: "Montserrat", sans-serif;
    font-weight: 700;
    font-size: 19px;
    line-height: 1.15;
    letter-spacing: 0.5px;
    color: var(--orange);
    text-transform: uppercase;
  }
  .brand-phone {
    font-family: "Lato", sans-serif;
    font-size: 17px;
    letter-spacing: 3px;
    color: var(--orange);
  }

  /* Back */
  .card--back {
    display: flex;
    flex-direction: column;
    align-items: center;
    justify-content: center;
    text-align: center;
    padding-bottom: 9px;
    font-family: "Lato", sans-serif;
  }
  .contact-name {
    font-family: "Montserrat", sans-serif;
    font-weight: 700;
    font-size: 19px;
    color: var(--orange);
    text-transform: uppercase;
    margin-bottom: 12px;
  }
  .contact-line {
    font-size: 14px;
    color: var(--light-grey);
    line-height: 1.7;
  }
  .contact-rule {
    width: 260px;
    height: 1px;
    background: var(--rule);
    margin: 12px 0;
  }
  .tagline {
    font-size: 14px;
    color: var(--orange);
    text-transform: uppercase;
    letter-spacing: 0.3px;
    margin-bottom: 6px;
  }
  .services {
    font-size: 14px;
    color: var(--light-grey);
    line-height: 1.5;
  }
</style>
</head>
<body>
<main class="canvas">
  <section class="card card--front" aria-label="Business card front">
    <div class="brand-mark"></div>
    <div class="brand-divider"></div>
    <div class="brand-text">
      <p class="brand-name">Holloway Paving<br>Service</p>
      <p class="brand-phone">0418259730</p>
    </div>
    <div class="card__band"></div>
  </section>

  <section class="card card--back" aria-label="Business card back">
    <h1 class="contact-name">Mark Holloway</h1>
    <p class="contact-line">ABN 62318470915</p>
    <p class="contact-line">markholloway@brightmail.com.au</p>
    <div class="contact-rule"></div>
    <p class="tagline">For all your concreting solutions</p>
    <p class="services">Excavation &nbsp;| Exposed &amp; colour concrete</p>
    <p class="services">House &amp; shed slabs | Driveways | Landing &amp; steps</p>
    <div class="card__band"></div>
  </section>
</main>
</body>
</html>
```